Pitch Deck Powerpoint Template for Entrepreneurship/Education Based Nonprofit

I need a stylish powerpoint design for a start-up nonprofit called Harbor Venture Works (HVW). I am building HVWs pitch deck to raise money. HVW is an entrepreneurial incubator and accelerator that seeks to identify, validate, test, and launch innovative ventures that improve public education. An example of our model, and one of our partners, is Kestrel Schools in New Orleans and New York :http://kestrelsch.example.org

We need the deck to look sleek and innovative - like a start-up pitch deck. Lots of different templates and fonts that pop off the page.

Target Market(s)

Individuals, foundations, and any other stakeholder - we are pitching a new business model and asking for money.

Industry/Entity Type

Building

Font styles to use
Sans Serif

Requirements
Must have
• A sleek/modern feel with several different template slides. charts and graphs/ strong fonts that pop off the page, use of the logo:
• It would be great to have a slide describing the 3 primary programs at Harbor Venture Works (HVW):
• - HVWspark - come in with an idea for an innovation in education, and we will do a two day workshop to examine your business assumptions and discuss next steps.
• - HVWpropell - take your idea to a prototype and launch to customers - we help you with an intensive 30 day program
• - HVWnurture - for existing nonprofit projects, we allow you to work under our umbrella to launch and build capacity
• Slides: Problem Definition, Solution, Value Proposition, Data/MEasurement, Key Partners, About the founder, Key Advisors

```html
<!DOCTYPE html>
<html lang="en">
<head>
<meta charset="utf-8">
<title>Key Advisors – Harbor Venture Works</title>
<link rel="stylesheet" href="https://fonts.googleapis.com/css2?family=Open+Sans:wght@400;600;700&family=Oswald:wght@400;500&display=swap">
<style>
  :root {
    --stage: #000000;
    --paper: #ffffff;
    --navy: #00447c;
    --magenta: #a9218e;
    --ink: #111111;
    --folio: #0b4a8c;
  }
  * { margin: 0; padding: 0; box-sizing: border-box; }
  html, body { width: 1200px; height: 1100px; overflow: hidden; background: var(--stage); }
  .sheet { position: relative; width: 1200px; height: 1100px; font-family: "Open Sans", sans-serif; }
  .sheet-title {
    position: absolute; top: 92px; left: 0; width: 1200px; text-align: center;
    color: var(--paper); font-weight: 600; font-size: 32px; line-height: 46px;
  }
  .sheet-number {
    position: absolute; top: 1046px; right: 22px; color: var(--folio);
    font-size: 32px; line-height: 40px;
  }
  .slide {
    position: absolute; left: 88px; top: 166px; width: 1024px; height: 768px;
    background: var(--paper); overflow: hidden;
  }
  .title-band {
    position: absolute; left: 0; top: 43px; width: 733px; height: 94px; background: var(--navy);
  }
  .title-band h1 {
    position: absolute; left: 45px; top: 20px; color: var(--paper);
    font-family: "Oswald", sans-serif; font-weight: 400; font-size: 44px; line-height: 56px;
    letter-spacing: -0.5px; transform: scaleX(0.96); transform-origin: left center;
    white-space: nowrap;
  }
  .brand {
    position: absolute; left: 760px; top: 40px; display: flex; align-items: flex-start; gap: 8px;
  }
  .brand-dot { width: 14px; height: 14px; border-radius: 50%; background: var(--magenta); margin-top: 8px; }
  .brand-name {
    color: var(--navy); font-weight: 700; font-size: 30px; line-height: 31px; letter-spacing: -0.3px;
  }
  .advisor { position: absolute; left: 52px; width: 930px; height: 140px; }
  .advisor-photo { position: absolute; left: 0; top: 0; width: 150px; height: 140px; }
  .advisor-photo text { font-family: "Open Sans", sans-serif; font-size: 15px; fill: var(--ink); }
  .advisor-name {
    position: absolute; left: 165px; top: 12px; color: var(--ink);
    font-weight: 600; font-size: 20px; line-height: 28px;
  }
  .advisor-bio {
    position: absolute; left: 165px; top: 54px; width: 761px; color: var(--ink);
    font-size: 15.5px; line-height: 21.5px;
  }
  .bio-line { display: block; white-space: nowrap; text-align: justify; text-align-last: justify; }
  .bio-line.last { text-align-last: left; }
  .footer { position: absolute; left: 0; top: 680px; width: 1024px; height: 88px; background: var(--magenta); }
  .footer-rule { position: absolute; left: 0; top: 0; width: 1024px; height: 6px; background: var(--navy); }
  .footer-page, .footer-url {
    position: absolute; top: 34px; color: var(--paper); font-weight: 700; font-size: 24px; line-height: 32px;
  }
  .footer-page { left: 45px; }
  .footer-url { right: 54px; }
</style>
</head>
<body>
<main class="sheet">
  <h2 class="sheet-title">Key Advisors</h2>

  <section class="slide">
    <header class="title-band"><h1>KEY ADVISORS</h1></header>
    <div class="brand">
      <span class="brand-dot"></span>
      <span class="brand-name">Harbor<br>Venture<br>Works</span>
    </div>

    <article class="advisor" style="top:175px">
      <svg class="advisor-photo" viewBox="0 0 150 140">
        <path d="M119.5 23.5 A68 68 0 1 0 130.1 39.2 L138 34 Z" fill="none" stroke="#111" stroke-width="1"/>
        <text x="69" y="74" text-anchor="middle">Image</text>
      </svg>
      <h3 class="advisor-name">JORDAN REYES</h3>
      <p class="advisor-bio"><span class="bio-line">Lorem ipsum dolor sit amet, consectetuer adipiscing elit, sed diam nonummy nibh euismod tincidunt</span><span class="bio-line">ut laoreet dolore magna aliquam erat volutpat. Ut wisi enim ad minim veniam, quis nostrud exerci</span><span class="bio-line last">tation ullamcorper suscipit lobortis nisl ut aliquip ex ea.</span></p>
    </article>

    <article class="advisor" style="top:340px">
      <svg class="advisor-photo" viewBox="0 0 150 140">
        <path d="M119.5 23.5 A68 68 0 1 0 130.1 39.2 L138 34 Z" fill="none" stroke="#111" stroke-width="1"/>
        <text x="69" y="74" text-anchor="middle">Image</text>
      </svg>
      <h3 class="advisor-name">JORDAN REYES</h3>
      <p class="advisor-bio"><span class="bio-line">Lorem ipsum dolor sit amet, consectetuer adipiscing elit, sed diam nonummy nibh euismod tincidunt</span><span class="bio-line">ut laoreet dolore magna aliquam erat volutpat. Ut wisi enim ad minim veniam, quis nostrud exerci</span><span class="bio-line last">tation ullamcorper suscipit lobortis nisl ut aliquip ex ea.</span></p>
    </article>

    <article class="advisor" style="top:503px">
      <svg class="advisor-photo" viewBox="0 0 150 140">
        <path d="M119.5 23.5 A68 68 0 1 0 130.1 39.2 L138 34 Z" fill="none" stroke="#111" stroke-width="1"/>
        <text x="69" y="74" text-anchor="middle">Image</text>
      </svg>
      <h3 class="advisor-name">JORDAN REYES</h3>
      <p class="advisor-bio"><span class="bio-line">Lorem ipsum dolor sit amet, consectetuer adipiscing elit, sed diam nonummy nibh euismod tincidunt</span><span class="bio-line">ut laoreet dolore magna aliquam erat volutpat. Ut wisi enim ad minim veniam, quis nostrud exerci</span><span class="bio-line last">tation ullamcorper suscipit lobortis nisl ut aliquip ex ea.</span></p>
    </article>

    <footer class="footer">
      <span class="footer-rule"></span>
      <span class="footer-page">Page 1</span>
      <span class="footer-url">www.hvw.example.com</span>
    </footer>
  </section>

  <span class="sheet-number">24</span>
</main>
</body>
</html>
```